PlumVesta screens tidy up

We would like advice on how to better present the following home page and overview pages.

The existing website is functional, but the pages don't appear professionals and pleasing to the eye. We would specifically like feedback on alignment and padding of icons and text to make the screen more appealing and polished.

We are following the quartzline design system.

1 page

Sans Serif
• IBM Plex, Poppins

```html
<!DOCTYPE html>
<html lang="en">
<head>
<meta charset="utf-8">
<title>PlumVesta – Home and Campaign Overview</title>
<link href="https://fonts.googleapis.com/css2?family=Poppins:wght@400;500;600&family=Roboto:wght@300;400;500;700&display=swap" rel="stylesheet">
<style>
  :root{
    --stage:#d3d3d3;
    --sidebar:#2a2a2a;
    --topbar:#2b2b2b;
    --page:#ffffff;
    --accent:#ef8a2a;
    --ink:#222222;
    --muted:#7a7a7a;
    --line:#dedede;
    --track:#e3e3e3;
    --on-dark:#ffffff;
  }
  *{box-sizing:border-box;margin:0;padding:0}
  html,body{width:696px;height:1200px;overflow:hidden;background:var(--stage)}
  .artboard{position:absolute;left:0;top:0;width:1452px;height:2504px;transform:scale(.4793);transform-origin:0 0;font-family:"Roboto",sans-serif;color:var(--ink)}
  .screen{position:absolute;left:49px;width:1354px;height:1160px;background:var(--page);overflow:hidden}
  .screen--home{top:54px}
  .screen--overview{top:1290px}
  .sidebar{position:absolute;left:0;top:0;width:305px;height:100%;background:var(--sidebar);font-family:"Poppins",sans-serif;color:var(--on-dark)}
  .topbar{position:absolute;left:305px;top:0;right:0;height:116px;background:var(--topbar)}
  .avatar{position:absolute;right:53px;top:26px;width:64px;height:64px;border-radius:50%;background:radial-gradient(circle at 50% 40%,#c9a27f,#8a6a52 60%,#d9d2c6)}
  .brand{position:absolute;left:48px;top:36px;display:flex;align-items:center;gap:12px}
  .brand-dot{width:42px;height:42px;border-radius:50%;background:var(--accent)}
  .brand-name{font-size:27px;font-weight:600;letter-spacing:-.5px}
  .nav-item{position:absolute;left:30px;display:flex;align-items:center;gap:14px;font-size:19px;height:30px;transform:translateY(-50%)}
  .nav-item svg{width:28px;height:28px;stroke:var(--on-dark);fill:none;stroke-width:1.4}
  .nav-item.is-active{color:var(--accent)}
  .nav-item.is-active svg{stroke:var(--accent)}
  .nav-item--plain{left:71px}
  .nav-plus{position:absolute;left:284px;color:var(--accent);font-size:24px;font-weight:500;transform:translateY(-50%)}
  .nav-tab{position:absolute;left:280px;width:40px;height:40px;border-radius:50%;background:var(--page);transform:translateY(-50%)}
  .nav-tab svg{position:absolute;left:6px;top:11px;width:18px;height:14px;stroke:var(--accent);fill:none;stroke-width:2.4}
  .nav-chevron{position:absolute;left:250px;width:18px;height:14px;stroke:var(--accent);fill:none;stroke-width:2.4;transform:translateY(-50%)}
  .subnav{position:absolute;left:71px;font-size:15px;line-height:25px}
  .subnav .is-active{color:var(--accent)}
  .h-section{position:absolute;font-size:24px;font-weight:500;letter-spacing:.2px;transform:translateY(-50%)}
  .card{position:absolute;background:var(--page);box-shadow:0 2px 6px rgba(0,0,0,.12)}
  .card--outline{box-shadow:none;border:1px solid var(--line)}
  .tile{position:absolute;border:2px solid var(--accent);border-radius:6px;background:var(--page)}
  .icon{position:absolute;width:52px;height:52px;stroke:var(--accent);fill:none;stroke-width:1.6}
  .counter{position:absolute;width:102px;height:88px;border:2px solid var(--accent);border-radius:6px;display:flex;align-items:center;justify-content:center;gap:14px;font-size:30px;font-weight:500}
  .counter svg{width:22px;height:24px}
  .badge{position:absolute;border-radius:50%;background:var(--accent);display:flex;flex-direction:column;align-items:center;justify-content:center;color:var(--on-dark)}
  .badge svg{stroke:var(--on-dark);fill:none;stroke-width:1.5}
  .muted{color:var(--muted)}
  .abs{position:absolute}
</style>
</head>
<body>
<svg width="0" height="0" style="position:absolute">
  <symbol id="i-home" viewBox="0 0 28 28"><path d="M3 13 14 3l11 10M6 11v14h6v-7h4v7h6V11"/></symbol>
  <symbol id="i-bell" viewBox="0 0 28 28"><path d="M7 20V13a7 7 0 0 1 14 0v7l2 2H5zM12 24a2 2 0 0 0 4 0M4 7l3-3M24 7l-3-3"/></symbol>
  <symbol id="i-manage" viewBox="0 0 28 28"><circle cx="14" cy="10" r="5"/><circle cx="14" cy="10" r="2"/><path d="M4 26v-6h20v6M8 20v6M14 20v6M20 20v6"/></symbol>
  <symbol id="i-building" viewBox="0 0 28 28"><path d="M3 25V12l6-4 6 4v13M15 25V6l10 4v15M2 25h24M6 15h2M6 19h2M11 15h2M11 19h2M18 12h2M18 16h2M18 20h2"/></symbol>
  <symbol id="i-chart" viewBox="0 0 52 52"><path d="M3 4v44h46M10 47V33h6v14M20 47V28h6v19M30 47V24h6v23M40 47V18h6v29M8 24l12-12 8 6 16-14M38 4h6v6M10 4l-4 8h6l-4 8"/></symbol>
  <symbol id="i-doc" viewBox="0 0 52 52"><path d="M8 3h26l10 10v36H8zM34 3v10h10M14 20h24M14 26h24M14 32h24M14 38h24M14 44h18"/></symbol>
  <symbol id="i-check" viewBox="0 0 22 22"><circle cx="11" cy="11" r="9" fill="#222"/><path d="M6.5 11.5l3 3 6-6" stroke="#fff" stroke-width="2.2" fill="none"/></symbol>
  <symbol id="i-file" viewBox="0 0 22 24"><path d="M3 1h11l5 5v17H3zM14 1v5h5M6 10h10M6 13h10M6 16h10M6 19h10" stroke="#222" stroke-width="1.3" fill="none"/></symbol>
  <symbol id="i-folder" viewBox="0 0 50 40"><path d="M12 6h10l3 4h20v24H12z"/><circle cx="17" cy="26" r="7"/><circle cx="17" cy="26" r="2.5"/><circle cx="29" cy="19" r="5"/><circle cx="29" cy="19" r="1.8"/></symbol>
  <symbol id="i-chevup" viewBox="0 0 18 14"><path d="M2 11 9 4l7 7"/></symbol>
  <symbol id="i-chevdown" viewBox="0 0 18 14"><path d="M2 3l7 7 7-7"/></symbol>
</svg>

<div class="artboard">

  <!-- Home screen -->
  <section class="screen screen--home">
    <aside class="sidebar">
      <div class="brand"><span class="brand-dot"></span><span class="brand-name">PlumVesta</span></div>
      <div class="nav-item is-active" style="top:144px"><svg><use href="#i-home"/></svg>Home</div>
      <div class="nav-item" style="top:199px"><svg><use href="#i-bell"/></svg>All alerts</div>
      <div class="nav-item" style="top:254px"><svg><use href="#i-manage"/></svg>Manage</div>
      <div class="nav-item nav-item--plain" style="top:309px">Campaigns</div>
      <span class="nav-plus" style="top:309px">+</span>
      <div class="nav-item" style="top:364px"><svg><use href="#i-building"/></svg>My custom campaign</div>
      <span class="nav-tab" style="top:364px"><svg><use href="#i-chevup"/></svg></span>
      <div class="subnav" style="top:391px"><div>Overview</div><div>Files &amp; Honey Tokens</div><div>Rsources</div><div>Alerts</div><div>Settings</div></div>
      <div class="nav-item" style="top:557px"><svg><use href="#i-building"/></svg>Default campaign</div>
      <svg class="nav-chevron" style="top:557px"><use href="#i-chevdown"/></svg>
    </aside>
    <header class="topbar"><div class="avatar" role="img" aria-label="User profile photo"></div></header>

    <h2 class="h-section" style="left:369px;top:176px">Teamspace</h2>
    <div class="card card--outline" style="left:371px;top:207px;width:932px;height:130px">
      <div class="abs" style="left:26px;top:24px;font-size:29px">Default</div>
      <div class="abs" style="left:28px;top:77px;font-size:17px">The default client is created as a part of your user account.</div>
    </div>

    <h2 class="h-section" style="left:369px;top:416px">Subscription Overview</h2>
    <h2 class="h-section" style="left:861px;top:416px">Files &amp; HoneyTokens</h2>
    <div class="card" style="left:369px;top:460px;width:443px;height:247px">
      <svg class="icon" style="left:28px;top:26px"><use href="#i-chart"/></svg>
      <div class="abs" style="left:28px;top:111px;font-size:23px">Starter pack usage</div>
      <div class="abs" style="left:28px;top:160px;width:388px;height:8px;border-radius:4px;background:var(--track)"></div>
      <div class="abs muted" style="left:28px;top:182px;font-size:14px">0 files active out of 10 allowed</div>
    </div>
    <div class="card" style="left:861px;top:460px;width:443px;height:247px">
      <svg class="icon" style="left:28px;top:26px"><use href="#i-doc"/></svg>
      <div class="counter" style="left:30px;top:116px"><svg><use href="#i-check"/></svg>0</div>
      <div class="counter" style="left:176px;top:116px"><svg><use href="#i-file"/></svg>30</div>
    </div>

    <h2 class="h-section" style="left:369px;top:776px">Campaigns</h2>
    <div class="card" style="left:369px;top:833px;width:934px;height:267px">
      <div class="tile" style="left:43px;top:26px;width:367px;height:215px">
        <div class="abs" style="left:20px;top:14px;font-size:24px">My custom campaign</div>
        <div class="abs muted" style="left:21px;top:54px;font-size:15px">This is my custom campaign for fingding!</div>
        <div class="badge" style="left:21px;top:91px;width:82px;height:82px"><svg width="50" height="40"><use href="#i-folder"/></svg></div>
        <div class="abs" style="left:123px;top:100px;font-size:15px;line-height:26px">0 Active<br>Files and HoneyTokens</div>
        <div class="abs muted" style="left:123px;top:168px;font-size:15px">Active Since: Jul 25 2023 13:12</div>
      </div>
      <div class="tile" style="left:526px;top:26px;width:367px;height:215px">
        <div class="abs" style="left:20px;top:14px;font-size:24px">Default campaign</div>
        <div class="abs muted" style="left:21px;top:54px;font-size:15px;white-space:nowrap">Define your own mission, or combine different</div>
        <div class="badge" style="left:21px;top:91px;width:82px;height:82px"><svg width="50" height="40"><use href="#i-folder"/></svg></div>
        <div class="abs" style="left:123px;top:100px;font-size:15px;line-height:26px">0 Active<br>Files and HoneyTokens</div>
        <div class="abs muted" style="left:123px;top:168px;font-size:15px">Active Since: Jul 20 2023 12:17</div>
      </div>
    </div>
  </section>

  <!-- Campaign overview screen -->
  <section class="screen screen--overview">
    <aside class="sidebar">
      <div class="brand"><span class="brand-dot"></span><span class="brand-name">PlumVesta</span></div>
      <div class="nav-item" style="top:144px"><svg><use href="#i-home"/></svg>Home</div>
      <div class="nav-item" style="top:199px"><svg><use href="#i-bell"/></svg>All alerts</div>
      <div class="nav-item" style="top:254px"><svg><use href="#i-manage"/></svg>Manage</div>
      <div class="nav-item nav-item--plain" style="top:309px">Campaigns</div>
      <span class="nav-plus" style="top:309px">+</span>
      <div class="nav-item" style="top:364px"><svg><use href="#i-building"/></svg>My custom campaign</div>
      <span class="nav-tab" style="top:364px"><svg><use href="#i-chevup"/></svg></span>
      <div class="subnav" style="top:391px"><div class="is-active">Overview</div><div>Files &amp; Honey Tokens</div><div>Rsources</div><div>Alerts</div><div>Settings</div></div>
      <div class="nav-item" style="top:557px"><svg><use href="#i-building"/></svg>Default campaign</div>
      <svg class="nav-chevron" style="top:557px"><use href="#i-chevdown"/></svg>
    </aside>
    <header class="topbar"><div class="avatar" role="img" aria-label="User profile photo"></div></header>

    <h2 class="h-section" style="left:369px;top:175px">Campaign</h2>
    <div class="card" style="left:371px;top:207px;width:932px;height:130px">
      <div class="badge" style="left:36px;top:24px;width:82px;height:82px"><svg width="50" height="40"><use href="#i-folder"/></svg></div>
      <div class="abs" style="left:147px;top:28px;font-size:26px">My custom campaign</div>
      <div class="abs muted" style="left:148px;top:75px;font-size:18px">This is my custom campaign for finding!</div>
      <div class="abs" style="left:785px;top:45px;width:111px;height:39px;border:2px solid var(--accent);border-radius:8px;color:var(--accent);font-size:16px;display:flex;align-items:center;justify-content:center">Custom</div>
    </div>

    <h2 class="h-section" style="left:369px;top:394px">Campaign organisation</h2>
    <div class="card" style="left:369px;top:451px;width:934px;height:267px">
      <div class="tile" style="left:78px;top:46px;width:367px;height:174px">
        <div class="abs" style="left:21px;top:46px;font-size:20px;line-height:27px">Self-enabling Deliveables<br>Proprietary Limited</div>
        <div class="abs muted" style="left:20px;top:114px;font-size:15px">Standard</div>
        <div class="badge" style="left:260px;top:50px;width:80px;height:80px;font-size:20px;font-weight:700"><svg width="36" height="34" viewBox="0 0 36 34"><circle cx="18" cy="7" r="5"/><circle cx="8" cy="25" r="5"/><circle cx="28" cy="25" r="5"/><path d="M18 12v5M13 21l3-3M23 21l-3-3"/></svg>86</div>
      </div>
      <div class="tile" style="left:489px;top:46px;width:367px;height:174px">
        <div class="abs" style="left:21px;top:46px;font-size:20px;line-height:27px">Unleash bleeding-edge<br>mindshare</div>
        <div class="abs muted" style="left:20px;top:114px;font-size:15px">8 hours ago</div>
        <div class="badge" style="left:260px;top:50px;width:80px;height:80px;font-size:20px;font-weight:700"><svg width="36" height="34" viewBox="0 0 36 34"><circle cx="15" cy="10" r="5"/><circle cx="15" cy="10" r="1.8"/><circle cx="26" cy="8" r="3.5"/><path d="M4 28h8l8-4h10M4 22h6l8 2"/></svg>8</div>
      </div>
    </div>

    <h2 class="h-section" style="left:371px;top:792px">Files &amp; HoneyTokens</h2>
    <h2 class="h-section" style="left:741px;top:792px">Resources</h2>
    <h2 class="h-section" style="left:1041px;top:792px">Alerts</h2>
    <div class="card" style="left:371px;top:836px;width:332px;height:246px">
      <svg class="icon" style="left:28px;top:26px"><use href="#i-doc"/></svg>
      <div class="counter" style="left:30px;top:116px"><svg><use href="#i-check"/></svg>0</div>
      <div class="counter" style="left:176px;top:116px"><svg><use href="#i-file"/></svg>30</div>
    </div>
    <div class="card" style="left:741px;top:836px;width:263px;height:246px">
      <svg class="icon" style="left:28px;top:26px"><use href="#i-chart"/></svg>
      <p class="abs" style="left:29px;top:98px;width:217px;font-size:16px;line-height:27px;text-align:justify">Generate a collection of fic-tional organisations, Custom templates, Uploaded files and logos.</p>
    </div>
    <div class="card" style="left:1041px;top:836px;width:263px;height:246px">
      <svg class="icon" style="left:28px;top:26px"><use href="#i-chart"/></svg>
      <p class="abs" style="left:29px;top:110px;font-size:16px">Alert statistics will appear here</p>
    </div>
  </section>

</div>
</body>
</html>
```